Business card design for a dynamic IT consulting company

We need a business card design for a young firm, specialized in the Telecommunications/Consulting industry. The name of the company is Quindor and Partners Business Consulting Ltd. (Short name: Quindor and Partnes)
Quindor = solve read reverse, so we aim to be uncomplicated and solution-oriented. The small pipe in our logo is also related to the word solve. So we need a new business card design, which is simple, eye catching and something non traditional (I would probably prefer a square shaped design rather than a rectangle, but open for suggestions). Attached our logo.

Target Market(s)

Usually our customers are Tier1 Telecoms providers (Q-Netra, Palorix, etc) and their executives.

Industry/Entity Type

Business

Contact Information for Business Card

Name: Bence Tolnavari
Email: b.tolnavari@quindor.hu
Web: www.quindor.hu
Mobile: +36 30 518 2769
Title: Managing Director

Optional:
Company name: Quindor and Partners Ltd.
Address: 1087 Budapest, Tolvenka str. 28/C, Hungary

Font styles to use
Other font styles liked:
• helveticaneue_medium, Prime Regular are used now.

Colors

Designer to choose colors to be used in the design.

Requirements
Must have
• I would like to have a 2 sided design.
Nice to have
• I thought if we make the logo a bit bigger (without the company name), that could go to the back with the company name below. I though, if the pipe in the logo is somehow touchable on the business card, would be nice and unique.

```html
<!DOCTYPE html>
<html lang="en">
<head>
<meta charset="utf-8">
<title>Quindor and Partners – Business Card</title>
<link rel="stylesheet" href="https://fonts.googleapis.com/css2?family=Roboto:wght@400;500&display=swap">
<style>
  :root {
    --page: #d6d6d6;
    --card-front: #fbfbfb;
    --card-back: #1f1f1f;
    --blue: #1479c0;
    --magenta: #b0268f;
    --ink: #3c3c3c;
    --rule: #a9a9a9;
    --icon-grey: #4a4a4a;
    --back-mark: #6e6e6e;
  }
  * { margin: 0; padding: 0; box-sizing: border-box; }
  html, body { width: 1200px; height: 1134px; overflow: hidden; }
  body {
    background: var(--page);
    font-family: "Roboto", Arial, sans-serif;
    color: var(--ink);
    position: relative;
  }
  .card {
    position: absolute;
    left: 261px;
    width: 675px;
    border-radius: 16px;
  }
  .card--front { top: 161px; height: 381px; background: var(--card-front); }
  .card--back  { top: 589px; height: 384px; background: var(--card-back); }

  .brand {
    position: absolute;
    left: 35px; top: 52px;
    display: flex; align-items: center; gap: 12px;
  }
  .brand__square { width: 22px; height: 22px; background: var(--blue); }
  .brand__name {
    font-size: 32px; font-weight: 400; color: var(--ink); letter-spacing: 0.5px;
  }

  .person { position: absolute; left: 35px; top: 181px; }
  .person__name { font-size: 28px; font-weight: 500; line-height: 34px; }
  .person__first { color: var(--blue); }
  .person__last { color: var(--magenta); }
  .person__title { font-size: 19px; line-height: 24px; color: var(--ink); }

  .rule {
    position: absolute; left: 35px; right: 41px; top: 249px;
    height: 2px; background: var(--rule);
  }

  .contacts { position: absolute; left: 35px; top: 270px; list-style: none; }
  .contacts li {
    display: flex; align-items: center; gap: 10px;
    height: 26px; font-size: 16px; color: var(--ink);
  }
  .contacts svg { width: 20px; height: 20px; flex: none; }

  .address {
    position: absolute; right: 41px; top: 279px;
    text-align: right; font-size: 16px; line-height: 22px; color: var(--ink);
  }
  .address__company { color: var(--blue); }

  .back-brand {
    position: absolute; left: 0; right: 0; top: 222px;
    display: flex; justify-content: center; align-items: center; gap: 14px;
  }
  .back-brand__square { width: 26px; height: 26px; background: var(--back-mark); }
  .back-brand__name { font-size: 40px; font-weight: 400; color: var(--back-mark); letter-spacing: 0.5px; }
</style>
</head>
<body>
  <section class="card card--front" aria-label="Business card front">
    <div class="brand">
      <span class="brand__square"></span>
      <span class="brand__name">Quindor &amp; Partners</span>
    </div>

    <div class="person">
      <p class="person__name"><span class="person__first">Bence</span> <span class="person__last">Tolnavari</span></p>
      <p class="person__title">Managing Director</p>
    </div>

    <div class="rule"></div>

    <ul class="contacts">
      <li>
        <svg viewBox="0 0 20 20" aria-hidden="true"><rect width="20" height="20" rx="3" fill="#1f9ad6"/><path d="M6 4.5l2 0 1 3-1.4 1.1a7 7 0 0 0 3.8 3.8L12.5 11l3 1v2c0 .8-.7 1.5-1.5 1.5A10 10 0 0 1 4.5 6c0-.8.7-1.5 1.5-1.5z" fill="#fff"/></svg>
        802.417.3096
      </li>
      <li>
        <svg viewBox="0 0 20 20" aria-hidden="true"><rect width="20" height="20" rx="3" fill="#b0268f"/><rect x="4" y="6" width="12" height="8" fill="none" stroke="#fff" stroke-width="1.3"/><path d="M4 6l6 5 6-5" fill="none" stroke="#fff" stroke-width="1.3"/></svg>
        b.tolnavari@quindor.hu
      </li>
      <li>
        <svg viewBox="0 0 20 20" aria-hidden="true"><rect width="20" height="20" rx="3" fill="#4a4a4a"/><circle cx="10" cy="10" r="5.5" fill="none" stroke="#fff" stroke-width="1.3"/><path d="M4.5 10h11M10 4.5c-2.5 3-2.5 8 0 11M10 4.5c2.5 3 2.5 8 0 11" fill="none" stroke="#fff" stroke-width="1"/></svg>
        www.quindor.hu
      </li>
    </ul>

    <address class="address" style="font-style:normal">
      <span class="address__company">Quindor and Partners Ltd</span><br>
      1087 Budapest,<br>
      Tolvenka str. 28/C, Hungary
    </address>
  </section>

  <section class="card card--back" aria-label="Business card back">
    <div class="back-brand">
      <span class="back-brand__square"></span>
      <span class="back-brand__name">Quindor &amp; Partners</span>
    </div>
  </section>
</body>
</html>
```